LLC needs a business card design that emphasizes consulting and expert witness in upstream oil and g

I need a business card design for my company called Obena Consultative Service, LLC. My expertise is in oil and gas upstream operations management to optimize performance and also as an expert witness for law firms in oil and gas upstream operations litigation.
The final design should communicate knowledge and hands-on experience as well as trust. (Obena means rope or lasso. Perhaps "Obena" should be in the form of a rope.) I do not like the color green in any shade. My first preference would be some shade of blue.
Industry/Entity Type
Oil And Gas

```html
<!DOCTYPE html>
<html lang="en">
<head>
<meta charset="utf-8">
<title>Obena Consultative Service, LLC — Business Card</title>
<link rel="stylesheet" href="https://fonts.googleapis.com/css2?family=Open+Sans:wght@400;600&family=Oswald:wght@400&display=swap">
<style>
  :root {
    --backdrop: #2b2724;
    --card: #161616;
    --card-edge: #0c0c0c;
    --ink: #ffffff;
    --ink-soft: #cfcfcf;
    --rule: #3c3c3c;
  }
  * { box-sizing: border-box; margin: 0; padding: 0; }
  html, body {
    width: 1200px;
    height: 844px;
    overflow: hidden;
    background: var(--backdrop);
  }
  .canvas {
    position: relative;
    width: 1200px;
    height: 844px;
    display: flex;
    align-items: center;
    justify-content: center;
    gap: 50px;
  }
  .card {
    position: relative;
    width: 525px;
    height: 300px;
    background: var(--card);
    border: 1px solid var(--card-edge);
    box-shadow: 0 10px 30px rgba(0,0,0,0.45);
    color: var(--ink);
  }

  /* Contact side */
  .card--contact .brand-name {
    position: absolute;
    left: 0;
    width: 300px;
    top: 0;
    height: 100%;
    display: flex;
    align-items: center;
    justify-content: center;
    font-family: "Open Sans", sans-serif;
    font-weight: 400;
    font-size: 54px;
    letter-spacing: 1px;
  }
  .card--contact .divider {
    position: absolute;
    left: 300px;
    top: 40px;
    bottom: 40px;
    width: 1px;
    background: var(--rule);
  }
  .contact {
    position: absolute;
    left: 325px;
    top: 78px;
    font-family: "Open Sans", sans-serif;
    color: var(--ink-soft);
    font-size: 12px;
    line-height: 1.4;
  }
  .contact .person {
    font-size: 19px;
    font-weight: 600;
    color: var(--ink);
    line-height: 1.15;
  }
  .contact .role {
    font-size: 11px;
    margin-bottom: 16px;
  }
  .contact .lines { margin-bottom: 12px; }

  /* Brand side */
  .card--brand {
    display: flex;
    flex-direction: column;
    align-items: center;
    justify-content: center;
  }
  .card--brand .brand-name {
    font-family: "Open Sans", sans-serif;
    font-weight: 400;
    font-size: 72px;
    line-height: 1;
    letter-spacing: 1px;
  }
  .card--brand .brand-descriptor {
    margin-top: 22px;
    font-family: "Oswald", sans-serif;
    font-size: 24px;
    letter-spacing: 1px;
    text-transform: uppercase;
  }
</style>
</head>
<body>
  <main class="canvas">
    <section class="card card--contact" aria-label="Contact side">
      <div class="brand-name">Obena</div>
      <div class="divider"></div>
      <div class="contact">
        <p class="person">Daniel Reyes</p>
        <p class="role">Managing Director</p>
        <div class="lines">
          <p>T: 044-310 552 870</p>
          <p>E: info@obenaservice.com</p>
          <p>W: www.obenaservice.com</p>
        </div>
        <p>4820, Ridge Park Road</p>
        <p>Houston, TX 77002.</p>
      </div>
    </section>

    <section class="card card--brand" aria-label="Brand side">
      <div class="brand-name">Obena</div>
      <div class="brand-descriptor">Consultative Service, LLC</div>
    </section>
  </main>
</body>
</html>
```